Animal Eye Clinic needs a Business card

We are a new veterinary ophthalmology practice (Ridgeline Pet Vision Care) and we need a business card designed. We only see animal eyes - we are not a regular veterinary clinic. We already have a logo. We are looking for a professional, good looking business card to hand out to our clients. We are looking for something simple but professional and contemporary. Our logo is likely the only picture/graphic that needs to be on the card.
Updates

Contact Information for Business Card

Delia Vossman, BSc, DVM, MSc, DipACVO
Veterinary Ophthalmologist

Phone: 250.418.3927
Email: ridgelinepetvisioncare@mailbox-example.net
Website: ridgelinepetvisioncare-example.net
Address: 1874 Thornbury Rd
Kelowna, BC, V1X 4M9

Colors

Designer to choose colors to be used in the design.

Requirements
Must have
• Our logo (attached)

```html
<!DOCTYPE html>
<html lang="en">
<head>
<meta charset="utf-8">
<title>Ridgeline Pet Vision Care – Business Card</title>
<link href="https://fonts.googleapis.com/css2?family=Open+Sans:wght@400;600;700&display=swap" rel="stylesheet">
<style>
  :root {
    --teal: #0397a8;
    --grey: #6f6f70;
    --ink: #333333;
    --muted: #5a5a5a;
    --paper: #ffffff;
    --backdrop: #d6d6d6;
  }
  * { margin: 0; padding: 0; box-sizing: border-box; }
  html, body {
    width: 1200px; height: 802px; overflow: hidden;
    background: var(--backdrop);
    font-family: "Open Sans", Arial, sans-serif;
  }
  .stage { position: relative; width: 1200px; height: 802px; }

  .card {
    position: absolute; top: 274px;
    width: 443px; height: 265px;
    box-shadow: 2px 4px 8px rgba(0,0,0,0.35);
    overflow: hidden;
  }
  .card--front { left: 136px; background: var(--paper); }
  .card--back  { left: 624px; background: var(--teal); }

  .card__waves { position: absolute; inset: 0; width: 443px; height: 265px; }

  .brand {
    position: absolute; display: flex; align-items: center; gap: 10px;
  }
  .brand__dot { border-radius: 50%; flex: none; }
  .brand__name { font-weight: 600; white-space: nowrap; letter-spacing: 0.2px; }

  .card--front .brand { left: 24px; top: 66px; }
  .card--front .brand__dot { width: 36px; height: 36px; background: var(--teal); }
  .card--front .brand__name { font-size: 17px; color: var(--teal); }

  .card--back .brand { left: 50%; top: 50%; transform: translate(-50%, -50%); gap: 14px; }
  .card--back .brand__dot { width: 52px; height: 52px; background: var(--paper); }
  .card--back .brand__name { font-size: 24px; color: var(--paper); }

  .person {
    position: absolute; right: 20px; top: 22px; text-align: right;
  }
  .person__name { font-size: 14.5px; font-weight: 700; color: var(--teal); letter-spacing: 0.2px; }
  .person__creds { font-size: 10.5px; color: var(--muted); margin-top: 2px; }
  .person__title { font-size: 10.5px; color: var(--ink); margin-top: 2px; }

  .contact {
    position: absolute; right: 18px; top: 155px; text-align: right;
    color: var(--paper); font-size: 10.5px; line-height: 16px;
  }
  .contact__address { margin-bottom: 5px; }
  .contact__line { display: flex; justify-content: flex-end; align-items: center; gap: 4px; }
  .contact__line--small { font-size: 10px; }
  .contact__icon { width: 10px; height: 10px; flex: none; }
</style>
</head>
<body>
<main class="stage">

  <section class="card card--front" aria-label="Business card front">
    <svg class="card__waves" viewBox="0 0 443 265" aria-hidden="true">
      <path d="M0 176 C40 200 80 215 120 210 C200 200 300 130 443 150 L443 265 L0 265 Z" fill="var(--teal)"/>
      <path d="M0 160 C30 185 70 200 110 196 C170 190 220 155 268 129 C220 150 170 185 112 190 C70 194 30 180 0 150 Z" fill="var(--grey)"/>
      <path d="M28 205 C80 230 150 212 230 180 C310 150 380 135 443 162" fill="none" stroke="var(--paper)" stroke-width="3"/>
      <path d="M0 196 C40 215 90 220 140 205" fill="none" stroke="var(--paper)" stroke-width="1.5" opacity="0.7"/>
    </svg>

    <div class="brand">
      <span class="brand__dot"></span>
      <span class="brand__name">Ridgeline Pet Vision Care</span>
    </div>

    <div class="person">
      <p class="person__name">DELIA VOSSMAN</p>
      <p class="person__creds">BSC, DVM, MSC, DIPACVO</p>
      <p class="person__title">Veterinary Ophthalmologist</p>
    </div>

    <div class="contact">
      <p class="contact__address">1874 Thornbury Rd<br>Kelowna, BC, V1X 4M9</p>
      <p class="contact__line">250.418.3927
        <svg class="contact__icon" viewBox="0 0 10 10" aria-hidden="true"><path d="M1 3 Q5 0 9 3 L8 4 L6.5 3.5 L6.5 4.5 L3.5 4.5 L3.5 3.5 L2 4 Z M2.5 5 L7.5 5 L8.5 9 L1.5 9 Z" fill="#fff"/></svg>
      </p>
      <p class="contact__line contact__line--small">ridgelinepetvisioncare@mailbox-example.net
        <svg class="contact__icon" viewBox="0 0 10 10" aria-hidden="true"><rect x="0.5" y="2" width="9" height="6.5" fill="#fff"/><path d="M0.5 2 L5 5.5 L9.5 2" fill="none" stroke="var(--teal)" stroke-width="0.9"/></svg>
      </p>
      <p class="contact__line contact__line--small">ridgelinepetvisioncare-example.net
        <svg class="contact__icon" viewBox="0 0 10 10" aria-hidden="true"><circle cx="5" cy="5" r="4.5" fill="#fff"/><path d="M5 0.5 V9.5 M0.5 5 H9.5 M5 0.5 C2.5 3 2.5 7 5 9.5 C7.5 7 7.5 3 5 0.5" fill="none" stroke="var(--teal)" stroke-width="0.7"/></svg>
      </p>
    </div>
  </section>

  <section class="card card--back" aria-label="Business card back">
    <div class="brand">
      <span class="brand__dot"></span>
      <span class="brand__name">Ridgeline Pet Vision Care</span>
    </div>
  </section>

</main>
</body>
</html>
```